Property Services Company Needs a Brochure Design

Looking for a new brochure design for an existing property services company.

We provide a range of property services from, market research, real estate brokerage, valuation and appraisal, property development and other real estate consulting services.

We would like a fresh modern brochure design with good graphics and features. Our colours are white, blue and orange.

The design should communicate, attention to detail, superior service delivery and distinction in results.
Updates

I would like the brochure to be roughly about 20 pages.

Containing the following,

1) An introduction
2) Contents Page
2) What we do
3) Our Services
4) Agency & Brokerage
5) Real Estate Consulting
6) Market Research
7) Appraisal & Valuation
8) Project Management
9) Property Development

I would also like icons to represent items 4,5,6,7,8 & 9, they should be represented vertically on each of the pages from the contents page and highlighted individually on the pages that they represent.. i.e. on appraisal & valuation page, all six icons will be arranged vertically and the appraisal and valuations icon will be highlighted.

I will also like to have images that depict the services on the various pages.

I have some pages I think will flow which I will upload shortly.

Industry/Entity Type

Real Estate

Font styles to use
Serif

Colors
f78f20
0455a3

```html
<!DOCTYPE html>
<html lang="en">
<head>
<meta charset="utf-8">
<title>Property Services Brochure – Service Spreads</title>
<link rel="stylesheet" href="https://fonts.googleapis.com/css2?family=Open+Sans:wght@300;400&display=swap">
<style>
  :root {
    --orange: #f78f20;
    --orange-deep: #e07b12;
    --blue: #0455a3;
    --blue-deep: #0a3a78;
    --ink: #2b2b2b;
    --icon: #e6e6e6;
    --stage: #1c1c1c;
  }
  * { margin: 0; padding: 0; box-sizing: border-box; }
  html, body { width: 1200px; height: 900px; overflow: hidden; background: var(--stage); }
  .canvas { position: relative; width: 1200px; height: 900px; font-family: "Open Sans", sans-serif; }
  .spread {
    position: absolute; left: 108px; width: 1007px; height: 355px;
    box-shadow: 0 6px 18px rgba(0,0,0,.6);
  }
  .spread--research { top: 78px; }
  .spread--projects { top: 478px; }
  .spread-shapes { position: absolute; inset: 0; width: 1007px; height: 355px; display: block; }
  .service-title {
    position: absolute; top: 15px; width: 300px; margin-left: -150px;
    text-align: center; color: #fff; font-weight: 300; font-size: 17px; letter-spacing: .3px;
    text-transform: uppercase;
  }
  .service-title--left { left: 335px; }
  .service-title--right { left: 738px; }
  .service-copy {
    position: absolute; color: var(--ink); font-weight: 400;
  }
  .service-copy p + p { margin-top: 12px; }
  .service-copy--left { left: 49px; top: 153px; width: 422px; font-size: 10px; line-height: 19px; }
  .service-copy--right { right: 12px; top: 154px; width: 290px; text-align: right; font-size: 9.8px; line-height: 17px; }
</style>
</head>
<body>
<div class="canvas">

  <!-- Spread: Market Research / Appraisal & Valuation -->
  <section class="spread spread--research">
    <svg class="spread-shapes" viewBox="0 0 1007 355" aria-hidden="true">
      <defs>
        <linearGradient id="pageLeft" x1="0" y1="0" x2="1" y2="1">
          <stop offset="0" stop-color="#ffffff"/><stop offset="1" stop-color="#d6d6d6"/>
        </linearGradient>
        <linearGradient id="pageRight" x1="0" y1="0" x2="1" y2="1">
          <stop offset="0" stop-color="#ffffff"/><stop offset="1" stop-color="#dcdcdc"/>
        </linearGradient>
        <linearGradient id="blueField" x1="0" y1="0" x2="1" y2="1">
          <stop offset="0" stop-color="#0455a3"/><stop offset="1" stop-color="#0a3a78"/>
        </linearGradient>
        <linearGradient id="lobbyTone" x1="0" y1="0" x2="0" y2="1">
          <stop offset="0" stop-color="#cfd3d4"/><stop offset=".5" stop-color="#9c9284"/><stop offset="1" stop-color="#d8d2c8"/>
        </linearGradient>
        <linearGradient id="orangeBand" x1="0" y1="0" x2="1" y2="0">
          <stop offset="0" stop-color="#f78f20"/><stop offset="1" stop-color="#e8841a"/>
        </linearGradient>
      </defs>
      <rect x="0" y="0" width="504" height="355" fill="url(#pageLeft)"/>
      <rect x="504" y="0" width="503" height="355" fill="url(#pageRight)"/>
      <rect x="0" y="0" width="27" height="355" fill="url(#blueField)"/>
      <rect x="27" y="0" width="477" height="52" fill="url(#orangeBand)"/>
      <rect x="41" y="0" width="101" height="134" fill="var(--orange-deep)"/>
      <!-- people with magnifier icon -->
      <g fill="var(--icon)">
        <circle cx="80" cy="28" r="6"/><rect x="72" y="36" width="16" height="22" rx="3"/>
        <circle cx="104" cy="28" r="6"/><rect x="96" y="36" width="16" height="22" rx="3"/>
        <circle cx="66" cy="56" r="6"/><rect x="58" y="64" width="16" height="48" rx="3"/>
        <circle cx="118" cy="56" r="6"/><rect x="110" y="64" width="16" height="48" rx="3"/>
        <rect x="80" y="82" width="24" height="30" rx="3"/>
      </g>
      <circle cx="92" cy="66" r="15" fill="var(--orange-deep)" stroke="var(--icon)" stroke-width="4"/>
      <circle cx="92" cy="62" r="4" fill="var(--icon)"/><path d="M84 74 q8 -8 16 0" fill="var(--icon)"/>
      <line x1="103" y1="77" x2="116" y2="92" stroke="var(--icon)" stroke-width="6" stroke-linecap="round"/>
      <!-- left page lower triangle -->
      <polygon points="342,355 504,355 504,204" fill="url(#blueField)"/>
      <line x1="342" y1="355" x2="504" y2="204" stroke="var(--orange)" stroke-width="5"/>
      <!-- right page -->
      <polygon points="540,0 1007,0 1007,52 593,52" fill="url(#orangeBand)"/>
      <polygon points="504,0 540,0 905,355 504,355" fill="url(#blueField)"/>
      <polygon role="img" aria-label="Photo: bright office lobby with marble floor" points="504,180 547,137 677,137 782,242 782,355 504,355" fill="url(#lobbyTone)"/>
      <line x1="504" y1="180" x2="611" y2="69" stroke="var(--orange)" stroke-width="4"/>
      <line x1="540" y1="0" x2="905" y2="355" stroke="var(--orange)" stroke-width="5"/>
      <rect x="898" y="0" width="102" height="134" fill="var(--orange-deep)"/>
      <!-- scales icon -->
      <g stroke="var(--icon)" stroke-width="3" fill="none">
        <line x1="949" y1="28" x2="949" y2="104"/>
        <line x1="917" y1="40" x2="981" y2="40"/>
        <path d="M917 40 l-11 30 h22 z"/><path d="M981 40 l-11 30 h22 z"/>
      </g>
      <g fill="var(--icon)">
        <path d="M906 70 a11 8 0 0 0 22 0 z"/><path d="M970 70 a11 8 0 0 0 22 0 z"/>
        <circle cx="949" cy="30" r="4"/><rect x="933" y="102" width="32" height="5" rx="2"/>
      </g>
    </svg>
    <h2 class="service-title service-title--left">Market Research</h2>
    <h2 class="service-title service-title--right">Appraisal &amp; Valuation</h2>
    <div class="service-copy service-copy--left">
      <p>Our market research team, regularly conduct surveys across a wide range of areas in both the commercial and residential markets. They regularly produce market reports that can be used for a wide range of purposes. This information also provides our team members with superior knowledge of market trends, price shifts, occupancy rates and other unique trends. The information provided allows us to provide information useful for forecasting growth and trends in the market.</p>
    </div>
    <div class="service-copy service-copy--right">
      <p>We provide valuation and appraisal services to clients<br>across a broad spectrum. Our valuation advice can<br>provide information to assist with portfolio<br>valuation, single asset valuation, financial<br>reporting valuation. These services are<br>provided to individuals, financial<br>institutions and corporates.<br>Appraisal methods will vary<br>based on the specific needs<br>of our clients</p>
    </div>
  </section>

  <!-- Spread: Project Management / Property Development -->
  <section class="spread spread--projects">
    <svg class="spread-shapes" viewBox="0 0 1007 355" aria-hidden="true">
      <defs>
        <linearGradient id="pageLeft2" x1="0" y1="0" x2="1" y2="1">
          <stop offset="0" stop-color="#ffffff"/><stop offset="1" stop-color="#d6d6d6"/>
        </linearGradient>
        <linearGradient id="pageRight2" x1="0" y1="0" x2="1" y2="1">
          <stop offset="0" stop-color="#ffffff"/><stop offset="1" stop-color="#dcdcdc"/>
        </linearGradient>
        <linearGradient id="blueField2" x1="0" y1="0" x2="1" y2="1">
          <stop offset="0" stop-color="#0455a3"/><stop offset="1" stop-color="#0a3a78"/>
        </linearGradient>
        <linearGradient id="siteTone" x1="0" y1="0" x2="0" y2="1">
          <stop offset="0" stop-color="#8fb6d8"/><stop offset=".45" stop-color="#c9a94a"/><stop offset="1" stop-color="#5b6b52"/>
        </linearGradient>
        <linearGradient id="orangeBand2" x1="0" y1="0" x2="1" y2="0">
          <stop offset="0" stop-color="#f78f20"/><stop offset="1" stop-color="#e8841a"/>
        </linearGradient>
      </defs>
      <rect x="0" y="0" width="504" height="355" fill="url(#pageLeft2)"/>
      <rect x="504" y="0" width="503" height="355" fill="url(#pageRight2)"/>
      <rect x="0" y="0" width="27" height="355" fill="url(#blueField2)"/>
      <rect x="27" y="0" width="477" height="52" fill="url(#orangeBand2)"/>
      <rect x="41" y="0" width="101" height="134" fill="var(--orange-deep)"/>
      <!-- cycle clock icon -->
      <rect x="50" y="30" width="83" height="83" rx="12" fill="#eeeeee"/>
      <g fill="none" stroke="var(--orange-deep)" stroke-width="7">
        <path d="M70 66 a22 22 0 0 1 38 -14"/><path d="M114 76 a22 22 0 0 1 -38 14"/>
      </g>
      <polygon points="102,44 116,44 114,58" fill="var(--orange-deep)"/>
      <polygon points="82,98 68,98 70,84" fill="var(--orange-deep)"/>
      <polyline points="92,60 92,72 100,76" fill="none" stroke="var(--orange-deep)" stroke-width="4" stroke-linecap="round"/>
      <polygon points="342,355 504,355 504,204" fill="url(#blueField2)"/>
      <line x1="342" y1="355" x2="504" y2="204" stroke="var(--orange)" stroke-width="5"/>
      <polygon points="540,0 1007,0 1007,52 593,52" fill="url(#orangeBand2)"/>
      <polygon points="504,0 540,0 905,355 504,355" fill="url(#blueField2)"/>
      <polygon role="img" aria-label="Photo: construction team in hard hats reviewing building plans" points="504,180 547,137 677,137 782,242 782,355 504,355" fill="url(#siteTone)"/>
      <line x1="504" y1="180" x2="611" y2="69" stroke="var(--orange)" stroke-width="4"/>
      <line x1="540" y1="0" x2="905" y2="355" stroke="var(--orange)" stroke-width="5"/>
      <rect x="896" y="0" width="104" height="134" fill="var(--orange-deep)"/>
      <!-- growth chart icon -->
      <g fill="var(--icon)">
        <rect x="912" y="86" width="12" height="22" rx="2"/>
        <rect x="928" y="74" width="12" height="34" rx="2"/>
        <rect x="944" y="80" width="12" height="28" rx="2"/>
        <rect x="960" y="62" width="12" height="46" rx="2"/>
        <polygon points="972,36 984,36 980,48"/>
      </g>
      <polyline points="912,70 930,54 948,62 978,40" fill="none" stroke="var(--icon)" stroke-width="4" stroke-linejoin="round"/>
    </svg>
    <h2 class="service-title service-title--left">Project Management</h2>
    <h2 class="service-title service-title--right">Property Developement</h2>
    <div class="service-copy service-copy--left">
      <p>Our project management team, with vast experience across commercial and residential developments provide the much needed support to achieve your dream property or office, allowing our clients to concentrate on their core business.</p>
      <p>We provide accurate information from financing, to design concept to budgeting<br>and construction management.</p>
    </div>
    <div class="service-copy service-copy--right">
      <p>We take pride in creating inspirational&nbsp; developments<br>that people can live, work and enjoy, whilst<br>adding value.</p>
    </div>
  </section>

</div>
</body>
</html>
```